Harrow Grading LLC business card design

Excavation company business cards

Contact Information for Business Card

Harrow Grading LLC cell phone 208-417-6290 office phone 208-319-4856 harrowgradingllc@maplecove.com Driveways, site prep, retaining walls, septic systems, rock delivery

Colors

Designer to choose colors to be used in the design.

```html
<!DOCTYPE html>
<html lang="en">
<head>
<meta charset="utf-8">
<title>Harrow Grading LLC — Business Card</title>
<link rel="stylesheet" href="https://fonts.googleapis.com/css2?family=Michroma&family=Roboto:wght@400;500&display=swap">
<style>
  :root {
    --orange: #e8701f;
    --orange-deep: #d9621a;
    --white: #ffffff;
    --ink-grey: #5a5a5a;
    --soft-grey: #b9b9b9;
    --backdrop: #2d2d2d;
  }
  * { margin: 0; padding: 0; box-sizing: border-box; }
  html, body { width: 1200px; height: 866px; overflow: hidden; background: var(--backdrop); }
  .canvas { position: relative; width: 1200px; height: 866px; }
  .card {
    position: absolute; left: 250px; width: 700px; height: 400px;
    overflow: hidden; box-shadow: 0 8px 22px rgba(0,0,0,.45);
  }
  .card--front { top: 22px; background: var(--white); }
  .card--back { top: 444px; background: var(--orange); }

  /* front */
  .front__backdrop {
    position: absolute; left: 0; top: 0; width: 380px; height: 320px;
    background: radial-gradient(ellipse at 35% 40%, rgba(0,0,0,.07), rgba(0,0,0,0) 70%);
  }
  .front__band { position: absolute; left: 0; bottom: 0; width: 700px; height: 110px; }
  .holder { position: absolute; left: 38px; top: 52px; }
  .holder__name {
    font-family: "Michroma", sans-serif; font-size: 22px; font-weight: 400; color: var(--orange);
    letter-spacing: 1px; text-transform: uppercase; white-space: nowrap;
  }
  .holder__title {
    font-family: "Roboto", sans-serif; font-size: 18px; color: var(--ink-grey);
    margin-top: 2px; letter-spacing: .5px;
  }
  .contact { position: absolute; left: 38px; top: 128px; list-style: none; }
  .contact__item {
    display: flex; align-items: center; gap: 10px;
    font-family: "Roboto", sans-serif; font-size: 18px; color: var(--ink-grey);
    line-height: 28px; letter-spacing: .4px; white-space: nowrap;
  }
  .contact__item svg { width: 18px; height: 18px; flex: none; }
  .front__rule {
    position: absolute; left: 38px; top: 226px; width: 630px; height: 1.5px; background: var(--orange);
  }
  .brand { position: absolute; text-align: center; font-family: "Michroma", sans-serif; text-transform: uppercase; white-space: nowrap; }
  .brand__main { font-size: 46px; letter-spacing: 2px; line-height: 1.1; }
  .brand__sub { font-size: 14px; letter-spacing: 9px; margin-top: 6px; }
  .brand--front { right: 40px; top: 118px; color: var(--orange); }
  .brand--front .brand__main { font-size: 38px; }
  .brand--front .brand__sub { font-size: 12px; letter-spacing: 8px; margin-top: 4px; }
  .address {
    position: absolute; right: 48px; top: 240px; text-align: left; font-style: normal;
    font-family: "Roboto", sans-serif; font-size: 18px; color: var(--ink-grey);
    line-height: 24px; letter-spacing: 1px;
  }

  /* back */
  .back__backdrop {
    position: absolute; left: 150px; top: 40px; width: 420px; height: 300px;
    background: radial-gradient(ellipse at center, rgba(255,255,255,.07), rgba(255,255,255,0) 70%);
  }
  .brand--back { left: 0; right: 0; top: 128px; color: var(--white); }
  .brand--back .brand__main { font-size: 60px; }
  .brand--back .brand__sub { font-size: 17px; letter-spacing: 12px; }
  .services {
    position: absolute; left: 0; right: 0; bottom: 40px; text-align: center;
    font-family: "Roboto", sans-serif; font-size: 18px; color: var(--white); letter-spacing: .6px;
  }
</style>
</head>
<body>
<main class="canvas">

  <section class="card card--front" aria-label="Card front">
    <div class="front__backdrop" role="img" aria-label="Faint grey machinery backdrop"></div>

    <div class="holder">
      <h1 class="holder__name">Daniel Mercer</h1>
      <p class="holder__title">Managing Director</p>
    </div>

    <ul class="contact">
      <li class="contact__item">
        <svg viewBox="0 0 18 18" aria-hidden="true"><rect x="5" y="1.5" width="8" height="15" rx="1.5" fill="none" stroke="#e8701f" stroke-width="1.6"/><line x1="8" y1="14" x2="10" y2="14" stroke="#e8701f" stroke-width="1.4"/></svg>
        208-417-6290
      </li>
      <li class="contact__item">
        <svg viewBox="0 0 18 18" aria-hidden="true"><path d="M5 2 L8 5 L6 7.5 C7 10 8 11 10.5 12 L13 10 L16 13 L13.5 16 C7 15 3 11 2 4.5 Z" fill="#e8701f"/></svg>
        208-319-4856
      </li>
      <li class="contact__item">
        <svg viewBox="0 0 18 18" aria-hidden="true"><rect x="1.5" y="4" width="15" height="10" fill="#e8701f"/><path d="M1.5 4 L9 10 L16.5 4" fill="none" stroke="#fff" stroke-width="1.3"/></svg>
        harrowgradingllc@maplecove.com
      </li>
    </ul>

    <div class="brand brand--front">
      <div class="brand__main">Harrow</div>
      <div class="brand__sub">Grading LLC</div>
    </div>

    <div class="front__rule"></div>

    <address class="address">421, Address line<br>goes here, 45452<br>Country Name</address>

    <svg class="front__band" viewBox="0 0 700 110" preserveAspectRatio="none" aria-hidden="true">
      <path d="M0 18 L300 96 L300 110 L0 110 Z" fill="#b9b9b9"/>
      <path d="M0 24 L280 100 C300 105 310 88 340 90 L700 96 L700 110 L0 110 Z" fill="#e8701f"/>
      <path d="M340 90 C310 88 300 105 280 100 L700 110 L700 96 Z" fill="#e8701f"/>
    </svg>
  </section>

  <section class="card card--back" aria-label="Card back">
    <div class="back__backdrop" role="img" aria-label="Faint embossed machinery backdrop"></div>
    <div class="brand brand--back">
      <div class="brand__main">Harrow</div>
      <div class="brand__sub">Grading LLC</div>
    </div>
    <p class="services">Driveways | Site prep | Retaining walls | Septic systems | Rock delivery</p>
  </section>

</main>
</body>
</html>
```